Harborlight Amusement Collective (HAC)

We need a business card design for Harborlight Amusement Collective. Modern and sleek looking, with all critical information. Open to single or double sided designs, if double sided info needs to be all on one side. The main Logo is Harborlight Amusement collective and must be on the card. The other three logos are for the brands that fall under the group, they might be good on the back.

Industry/Entity Type

Business

```html
<!DOCTYPE html>
<html lang="en">
<head>
<meta charset="utf-8">
<title>Harborlight Amusement Collective – Business Card</title>
<link href="https://fonts.googleapis.com/css2?family=Montserrat:wght@400;500;600;700&family=Roboto+Condensed:wght@700&display=swap" rel="stylesheet">
<style>
  :root {
    --bg: #d6d6d6;
    --card-white: #ffffff;
    --brand-blue: #2357a0;
    --brand-green: #8a9f2f;
    --ink: #2a2a2a;
    --muted: #555555;
    --white: #ffffff;
    --blue-tint: #3a6cb4;
  }
  * { margin: 0; padding: 0; box-sizing: border-box; }
  html, body { width: 1200px; height: 852px; overflow: hidden; }
  body {
    background: var(--bg);
    font-family: "Montserrat", Arial, sans-serif;
    position: relative;
  }
  .card {
    position: absolute;
    width: 540px;
    height: 320px;
    border-radius: 22px;
    overflow: hidden;
  }

  /* ---------- brand side ---------- */
  .card--brands {
    left: 40px; top: 140px;
    background: var(--card-white);
  }
  .wordmark { position: absolute; left: 0; right: 0; text-align: center; }
  .card--brands .wordmark { top: 34px; }
  .wordmark__badge {
    display: block;
    width: 46px; height: 46px;
    margin: 0 auto 12px;
    background: var(--brand-blue);
  }
  .wordmark__name {
    font-weight: 700;
    font-size: 24px;
    letter-spacing: 0.5px;
    color: var(--brand-blue);
    line-height: 1.05;
  }
  .wordmark__sub {
    display: flex; align-items: center; justify-content: center; gap: 14px;
    margin-top: 4px;
    font-weight: 600;
    font-size: 16px;
    letter-spacing: 9px;
    color: var(--brand-blue);
  }
  .wordmark__sub::before, .wordmark__sub::after {
    content: ""; width: 90px; height: 2px; background: var(--brand-blue);
  }
  .rule-green {
    position: absolute; height: 1.5px; background: var(--brand-green);
  }
  .brands-label {
    position: absolute; top: 168px; left: 0; right: 0;
    text-align: center; font-size: 12px; color: var(--ink);
  }
  .brand-row {
    position: absolute; top: 196px; left: 24px; right: 24px;
    display: flex; align-items: center; justify-content: space-between;
  }
  .brand {
    display: flex; align-items: center; gap: 7px;
    font-weight: 700; font-size: 17px; color: var(--brand-blue);
  }
  .brand__dot { width: 18px; height: 18px; border-radius: 50%; background: var(--brand-green); }
  .brand-divider { width: 1px; height: 40px; background: #999; }
  .site-url {
    position: absolute; top: 262px; left: 0; right: 0;
    text-align: center; font-size: 12.5px; color: var(--ink); letter-spacing: 0.3px;
  }

  /* ---------- contact side ---------- */
  .card--contact {
    left: 620px; top: 392px;
    background: var(--brand-blue);
    color: var(--white);
  }
  .decor-square {
    position: absolute; left: 34px; top: 92px;
    width: 200px; height: 200px;
    border: 12px solid var(--white);
    background: var(--blue-tint);
  }
  .card--contact .wordmark {
    top: 26px; left: auto; right: 26px; text-align: center; width: 290px;
  }
  .card--contact .wordmark__name { font-size: 15px; color: var(--white); }
  .card--contact .wordmark__sub {
    font-size: 11px; letter-spacing: 6px; color: var(--white); gap: 10px;
  }
  .card--contact .wordmark__sub::before,
  .card--contact .wordmark__sub::after { width: 60px; height: 1.5px; background: var(--white); }
  .contact {
    position: absolute; right: 26px; top: 100px; text-align: right;
  }
  .contact__name {
    font-family: "Roboto Condensed", "Arial Narrow", sans-serif;
    font-weight: 700; font-size: 22px;
  }
  .contact__role { font-size: 12px; margin-top: 2px; }
  .contact__list { list-style: none; margin-top: 18px; font-size: 12px; line-height: 1.55; }
  .contact__list li { display: flex; align-items: center; justify-content: flex-end; gap: 7px; }
  .contact__list svg { width: 12px; height: 12px; fill: var(--white); flex: none; }
  .contact__list .no-icon { padding-right: 19px; }
</style>
</head>
<body>

  <section class="card card--brands" aria-label="Brand side">
    <div class="wordmark">
      <span class="wordmark__badge"></span>
      <div class="wordmark__name">HARBORLIGHT AMUSEMENT</div>
      <div class="wordmark__sub">COLLECTIVE</div>
    </div>
    <span class="rule-green" style="top:174px;left:40px;width:170px;"></span>
    <span class="rule-green" style="top:174px;right:40px;width:170px;"></span>
    <p class="brands-label">Our Brands</p>
    <div class="brand-row">
      <span class="brand"><span class="brand__dot"></span>TidePass</span>
      <span class="brand-divider"></span>
      <span class="brand"><span class="brand__dot"></span>Boxseat Hospitality</span>
      <span class="brand-divider"></span>
      <span class="brand"><span class="brand__dot"></span>seatcorner</span>
    </div>
    <span class="rule-green" style="top:254px;left:40px;width:460px;"></span>
    <p class="site-url">www.harborlightamusement.com</p>
  </section>

  <section class="card card--contact" aria-label="Contact side">
    <span class="decor-square"></span>
    <div class="wordmark">
      <div class="wordmark__name">HARBORLIGHT AMUSEMENT</div>
      <div class="wordmark__sub">COLLECTIVE</div>
    </div>
    <div class="contact">
      <div class="contact__name">Jordan Avery Lane</div>
      <div class="contact__role">Managing Director</div>
      <ul class="contact__list">
        <li class="no-icon">418 Quayside Rd.,</li>
        <li class="no-icon">Port Marlow, US 204871</li>
        <li>555.014.2297
          <svg viewBox="0 0 24 24"><path d="M6.6 10.8a15 15 0 0 0 6.6 6.6l2.2-2.2c.3-.3.7-.4 1-.2 1.1.4 2.3.6 3.6.6.6 0 1 .4 1 1V20c0 .6-.4 1-1 1A17 17 0 0 1 3 4c0-.6.4-1 1-1h3.5c.6 0 1 .4 1 1 0 1.3.2 2.5.6 3.6.1.3 0 .7-.2 1z"/></svg>
        </li>
        <li>jordan@harborlightamusement.com
          <svg viewBox="0 0 24 24"><path d="M2 5h20v14H2zm2 2v.5l8 5 8-5V7l-8 5z"/></svg>
        </li>
        <li>www.harborlightamusement.com
          <svg viewBox="0 0 24 24"><path d="M12 2a10 10 0 1 0 0 20 10 10 0 0 0 0-20zm6.9 6h-3a15 15 0 0 0-1.3-3.9A8 8 0 0 1 18.9 8zM12 4c.8 1.2 1.5 2.5 1.9 4h-3.8c.4-1.5 1.1-2.8 1.9-4zM4.3 14a8 8 0 0 1 0-4h3.4a16 16 0 0 0 0 4zm.8 2h3a15 15 0 0 0 1.3 3.9A8 8 0 0 1 5.1 16zM8 8H5.1a8 8 0 0 1 4.3-3.9A15 15 0 0 0 8 8zm4 12c-.8-1.2-1.5-2.5-1.9-4h3.8c-.4 1.5-1.1 2.8-1.9 4zm2.3-6H9.7a14 14 0 0 1 0-4h4.6a14 14 0 0 1 0 4zm.3 5.9a15 15 0 0 0 1.3-3.9h3a8 8 0 0 1-4.3 3.9zm1.7-5.9a16 16 0 0 0 0-4h3.4a8 8 0 0 1 0 4z"/></svg>
        </li>
      </ul>
    </div>
  </section>

</body>
</html>
```